"Vine Hollow Excursions" is a top notch Santa Barbara County Wine Tour company.

We provide scenic, boutique and custom wine tours. I need the card to be clean and classy. I will provide our logo. I would like the logo to cover the back side of the card as an option and would like to see a couple color options other then our signature green and gold. I would like to see some creative options and let the designers come up with options.
I need cards for myself and my team. The final design should communicate "An authentic and boutique wine tour experience"
Please use my website for reference www.vinehollowexcursions.example

Target Market(s)

We have a wide range of clients from millennials to baby boomers

Industry/Entity Type

Tour

Contact Information for Business Card

Contact info:
Dale Morton
805-219-6384
info@vinehollowexcursions.example
vinehollowexcursions.example

Colors

Designer to choose colors to be used in the design.

Requirements
Must have
• my logo
Nice to have
• *I would like to have the backside side with the logo and the company statement
• "An authentic and boutique wine tour experience" as an option.
• *I would also like to see what the designers can create!
• *I would like to see an option that incorporates or social: instagram, yelp, trip advisor
Should not have
• I do not want it too busy.

```html
<!DOCTYPE html>
<html lang="en">
<head>
<meta charset="utf-8">
<title>Vine Hollow Excursions – Business Card</title>
<link href="https://fonts.googleapis.com/css2?family=Roboto+Condensed:wght@400;500&family=Roboto:wght@400&display=swap" rel="stylesheet">
<style>
  :root {
    --backdrop: #ecebe7;
    --card-light: #f4f4f4;
    --card-light-edge: #dcdcdc;
    --vine-green: #236844;
    --gold: #b39c7d;
    --gold-dark: #8f7a5e;
    --ink: #4a4a4a;
    --icon: #8d8d8d;
    --rule: #5a5a5a;
    --badge: #4f8a68;
  }
  * { box-sizing: border-box; margin: 0; padding: 0; }
  html, body { width: 1200px; height: 960px; overflow: hidden; }
  body {
    background: var(--backdrop);
    position: relative;
    font-family: "Roboto", Arial, sans-serif;
  }
  .card {
    position: absolute;
    width: 600px;
    height: 343px;
    box-shadow: 0 3px 8px rgba(0,0,0,0.25);
  }
  .card-front {
    left: 302px; top: 129px;
    background: linear-gradient(90deg, #fbfbfb 0%, var(--card-light) 45%, var(--card-light-edge) 100%);
  }
  .card-back {
    left: 300px; top: 488px;
    background: var(--vine-green);
  }
  .front-brand {
    position: absolute;
    left: 40px; top: 100px;
    display: flex; align-items: center; gap: 10px;
  }
  .brand-square {
    width: 14px; height: 14px;
    background: var(--vine-green);
  }
  .front-brand .brand-name {
    font-family: "Roboto Condensed", Arial, sans-serif;
    font-weight: 500;
    font-size: 25px;
    color: var(--vine-green);
    letter-spacing: 0.5px;
  }
  .contact-block {
    position: absolute;
    right: 42px; top: 204px;
    text-align: right;
  }
  .person-name {
    font-family: "Roboto Condensed", Arial, sans-serif;
    font-weight: 500;
    font-size: 28px;
    color: var(--gold-dark);
    padding-bottom: 6px;
    border-bottom: 1px solid var(--rule);
    padding-left: 34px;
    display: inline-block;
  }
  .contact-list { list-style: none; margin-top: 10px; }
  .contact-list li {
    display: flex; justify-content: flex-end; align-items: center;
    gap: 8px;
    font-size: 14.5px;
    color: var(--ink);
    line-height: 19.5px;
  }
  .contact-list svg { width: 13px; height: 13px; fill: var(--icon); flex: none; }
  .back-brand {
    position: absolute;
    left: 0; right: 0; top: 128px;
    text-align: center;
    font-family: "Roboto Condensed", Arial, sans-serif;
    font-weight: 500;
    font-size: 44px;
    color: var(--gold);
    letter-spacing: 1px;
  }
  .tagline {
    position: absolute;
    left: 0; right: 0; top: 219px;
    text-align: center;
    font-family: "Roboto Condensed", Arial, sans-serif;
    font-size: 15.5px;
    color: var(--gold);
  }
  .social-row {
    position: absolute;
    left: 0; right: 0; top: 282px;
    display: flex; justify-content: center; gap: 7px;
  }
  .social-badge {
    width: 26px; height: 26px;
    border-radius: 4px;
    background: var(--badge);
    border: 1px solid rgba(255,255,255,0.35);
  }
</style>
</head>
<body>
  <section class="card card-front" aria-label="Card front">
    <div class="front-brand">
      <span class="brand-square"></span>
      <span class="brand-name">Vine Hollow Excursions</span>
    </div>
    <div class="contact-block">
      <h1 class="person-name">DALE MORTON</h1>
      <ul class="contact-list">
        <li>805-219-6384
          <svg viewBox="0 0 16 16" aria-hidden="true"><path d="M3.6 1.2l2.3 2.4-1.2 2c.9 2 2.6 3.7 4.6 4.6l2-1.2 2.4 2.3-1.3 2.3C7 13.8 2.2 9 1.3 2.5z"/></svg>
        </li>
        <li>info@vinehollowexcursions.example
          <svg viewBox="0 0 16 16" aria-hidden="true"><path d="M1 3h14v10H1zm1.2 1.2L8 8.5l5.8-4.3z"/></svg>
        </li>
        <li>vinehollowexcursions.example
          <svg viewBox="0 0 16 16" aria-hidden="true"><circle cx="8" cy="8" r="7"/></svg>
        </li>
      </ul>
    </div>
  </section>

  <section class="card card-back" aria-label="Card back">
    <p class="back-brand">Vine Hollow Excursions</p>
    <p class="tagline">An authentic &amp; boutique wine tour experience</p>
    <div class="social-row" aria-label="Social profiles">
      <span class="social-badge"></span>
      <span class="social-badge"></span>
      <span class="social-badge"></span>
      <span class="social-badge"></span>
      <span class="social-badge"></span>
    </div>
  </section>
</body>
</html>
```